Mobile Fitness snd Therapy Business Card Design

I need a business card designed for my mobile fitness and therapy business.

Please view the images that I have uploaded. I like the simplicity of the design that I have attached. I adapted it with my information

Target Market(s)

Those seeking personal training, injury rehabilitation or massage therapy.

Industry/Entity Type

Business

Contact Information for Business Card

Derek Fulham - MSc, CAT(C), RMT, CSCS, Pn2
e-mail: derek@vantrelo.com
website: www.vantrelo.com
instagram: @derek_fulham

Font styles to use
Sans Serif

Colors
3176b5
0355a3

Requirements
Must have
• "Contact us to receive a FREE assessment"
• Services offered:
• Personal Training
• Golf Fitness
• Injury Rehab
• Massage Therapy
• Yoga
Nice to have
• Consistent colours with brand
• - Dark Blue: #232837
• - Blue: #5096f0
• Consistent look/feel with the website: www.vantrelo.com

```html
<!DOCTYPE html>
<html lang="en">
<head>
<meta charset="utf-8">
<title>Vantrelo Business Card</title>
<link href="https://fonts.googleapis.com/css2?family=Arimo:wght@400;700&display=swap" rel="stylesheet">
<style>
  :root {
    --stage: #555555;
    --paper: #ffffff;
    --ink: #1e2230;
    --ink-soft: #333333;
    --brand-blue: #2456d3;
    --band-dark: #2a5bd7;
    --band-light: #5a9bf0;
    --rule: #bdbdbd;
    --back-top: #232837;
    --back-bottom: #1d212c;
  }
  * { margin: 0; padding: 0; box-sizing: border-box; }
  html, body { width: 1200px; height: 900px; overflow: hidden; }
  body {
    background: var(--stage);
    font-family: "Arimo", Arial, sans-serif;
    position: relative;
  }
  .card {
    position: absolute;
    top: 170px;
    width: 347px;
    height: 561px;
    box-shadow: 3px 4px 8px rgba(0,0,0,0.35);
  }
  .card-front { left: 259px; background: var(--paper); text-align: center; color: var(--ink-soft); }
  .card-back {
    left: 631px;
    background: linear-gradient(180deg, var(--back-top) 0%, var(--back-bottom) 100%);
  }
  .block { position: absolute; left: 0; width: 100%; }
  .wordmark {
    top: 86px;
    font-size: 42px;
    font-weight: 700;
    letter-spacing: 3px;
    color: var(--ink);
    line-height: 1;
  }
  .tagline {
    top: 134px;
    font-size: 12.5px;
    font-weight: 700;
    letter-spacing: 1.6px;
    color: var(--ink);
  }
  .person-name {
    top: 217px;
    font-size: 20px;
    font-weight: 700;
    color: var(--brand-blue);
  }
  .credentials { top: 243px; font-size: 15px; }
  .rule {
    position: absolute;
    left: 76px;
    width: 194px;
    height: 1px;
    background: var(--rule);
  }
  .rule-upper { top: 275px; }
  .rule-lower { top: 347px; }
  .contact-line { font-size: 15px; line-height: 22px; }
  .contact-list { top: 286px; }
  .label { color: var(--brand-blue); font-weight: 700; }
  .social { top: 357px; }
  .offer-band {
    position: absolute;
    top: 407px;
    height: 28px;
  }
  .offer-band-left { left: 0; width: 36px; background: var(--band-dark); }
  .offer-band-right { right: 0; width: 41px; background: var(--band-light); }
  .offer {
    top: 405px;
    font-size: 16px;
    font-weight: 700;
    line-height: 21px;
    color: var(--ink);
  }
  .services-heading {
    top: 468px;
    font-size: 16.5px;
    font-weight: 700;
    color: var(--brand-blue);
  }
  .services-list {
    top: 487px;
    font-size: 14px;
    line-height: 18px;
    color: var(--ink-soft);
  }
</style>
</head>
<body>
  <section class="card card-front">
    <div class="block wordmark">VANTRELO</div>
    <div class="block tagline">NUTRITION - FITNESS - HEALTH</div>

    <div class="block person-name">DEREK FULHAM</div>
    <div class="block credentials">MSc, CAT(C), RMT, CSCS, Pn2</div>
    <div class="rule rule-upper"></div>

    <div class="block contact-list">
      <p class="contact-line"><span class="label">E :</span>derek@vantrelo.com</p>
      <p class="contact-line"><span class="label">W :</span>www.vantrelo.com</p>
    </div>
    <div class="rule rule-lower"></div>

    <p class="block social contact-line"><span class="label">INSTAGRAM :</span> @derek_fulham</p>

    <div class="offer-band offer-band-left"></div>
    <div class="offer-band offer-band-right"></div>
    <p class="block offer">CONTACT US TO RECEIVE A<br>FREE ASSESSMENT</p>

    <p class="block services-heading">SERVICES OFFERED:</p>
    <p class="block services-list">PERSONAL TRAINING &nbsp;|&nbsp; GOLF FITNESS<br>INJURY REHAB | MASSAGE THERAPY<br>YOGA</p>
  </section>

  <section class="card card-back" role="img" aria-label="Card back: dark navy field with a pattern of faint vertical rounded bars"></section>
</body>
</html>
```